Professional Package for CPA Firm

We would like a stationery design for our new CPA Firm based in Atlanta, GA called 'Vale 8'. We work with investors to help grow investments, tax free. We would like the design to have a professional/minimal look with a 'wow' factor. We need 9.5″ x 4.125″, 9x12, and 10x13 mailing envelopes, business cards, and a letterhead. We have a logo that is already complete. For the letterhead, we would like to have space to put credentials at the bottom of the page

Industry/Entity Type

CPA, Accounting

```html
<!DOCTYPE html>
<html lang="en">
<head>
<meta charset="utf-8">
<title>Vale 8 — Stationery Set</title>
<link href="https://fonts.googleapis.com/css2?family=Montserrat:wght@700&family=Open+Sans:wght@400;600;700&display=swap" rel="stylesheet">
<style>
  :root{
    --backdrop:#e8e8e8;
    --paper:#f0f0f0;
    --ink:#1b1c1f;
    --text:#4a4b4f;
    --muted:#6b6c70;
    --brand:#2a93cf;
    --night:#1d1e21;
    --photo-dark:#3b3e44;
    --photo-light:#d4dbdf;
  }
  *{box-sizing:border-box;margin:0;padding:0}
  html,body{width:1200px;height:795px;overflow:hidden;background:var(--backdrop)}
  body{position:relative;font-family:"Open Sans",Arial,sans-serif;color:var(--text)}
  .sheet{position:absolute;background:var(--paper);box-shadow:0 1px 3px rgba(0,0,0,.08)}

  /* brand lockup */
  .brand{display:flex;flex-direction:column;align-items:center}
  .brand-row{display:flex;align-items:center;gap:.25em}
  .brand-square{display:block;width:.62em;height:.62em;background:var(--brand)}
  .brand-name{font-family:"Montserrat",Arial,sans-serif;font-weight:700;color:var(--ink);line-height:1;letter-spacing:.01em}
  .brand-tag{font-family:"Open Sans",Arial,sans-serif;color:var(--ink);letter-spacing:.08em;line-height:1.2}

  /* letterhead */
  .letterhead{left:292px;top:99px;width:293px;height:415px}
  .letterhead .brand{margin-top:62px;font-size:17px}
  .letterhead .brand-tag{font-size:5px;margin-top:1px}
  .letter-body{position:absolute;left:26px;right:26px;top:97px;font-size:5.4px;line-height:8px}
  .letter-body p{text-align:justify;margin-bottom:8px}
  .letter-body .salute{margin-bottom:8px}
  .letter-credentials{position:absolute;left:0;right:0;bottom:20px;text-align:center;font-size:5.6px;line-height:8.5px;color:var(--muted)}
  .contact-line{display:flex;justify-content:center;gap:6px;align-items:center}
  .contact-line span{display:inline-flex;align-items:center;gap:2px}
  .icon{width:6px;height:6px;fill:var(--ink)}

  /* presentation folder */
  .folder{left:636px;top:79px;width:346px;height:438px}
  .folder-spine{position:absolute;left:0;top:0;bottom:0;width:19px;border-right:1px solid #dadada;
    background:linear-gradient(90deg,#f4f4f4 0 3px,#e4e4e4 3px 4px,#f2f2f2 4px 8px,#e4e4e4 8px 9px,#efefef 9px)}
  .folder .brand{position:absolute;left:19px;right:0;top:78px;font-size:25px}
  .folder .brand-tag{font-size:7px;margin-top:2px}
  .folder-photo{position:absolute;left:0;right:0;top:139px;height:229px;
    background:linear-gradient(110deg,var(--photo-dark) 0 22%,#8c9096 34%,var(--photo-light) 50%,#c9a070 66%,#5f8fae 78%,var(--brand) 100%)}
  .folder-url{position:absolute;left:19px;right:0;top:394px;text-align:center;font-size:9.5px;letter-spacing:.12em;color:#55575b}
  .folder-url b{font-weight:400;color:var(--brand)}

  /* business card */
  .card-front{left:187px;top:550px;width:132px;height:75px;display:flex;align-items:center;padding:0 10px 0 18px}
  .card-front .brand{font-size:10px;width:48px}
  .card-front .brand-tag{font-size:2.6px;letter-spacing:.04em;margin-top:1px}
  .card-divider{width:1px;height:40px;background:var(--brand);margin:0 6px 0 8px}
  .card-details{font-size:3.1px;line-height:4.2px;color:var(--ink)}
  .card-name{font-weight:700;font-size:4.3px;line-height:5px}
  .card-role{font-weight:600;margin-bottom:2px}
  .card-back{left:187px;top:646px;width:132px;height:75px;background:linear-gradient(135deg,#3a3b3f,#2a2b2e)}

  /* envelopes */
  .envelope-plain{left:353px;top:561px;width:329px;height:157px}
  .envelope-plain .brand{position:absolute;left:24px;top:23px;font-size:14px;align-items:center}
  .envelope-plain .brand-tag{font-size:4.2px;margin-top:1px}
  .envelope-address{position:absolute;left:17px;top:70px;width:80px;text-align:center;font-size:5.4px;line-height:7px;color:var(--muted)}
  .envelope-flap{left:713px;top:561px;width:328px;height:157px}
  .flap-band{position:absolute;left:0;right:0;top:0;height:50px;background:var(--night);clip-path:polygon(0 0,100% 0,98% 100%,2% 100%)}
  .flap-band .brand{position:absolute;left:0;right:0;top:17px;font-size:9px}
  .flap-band .brand-name{color:#fff}
  .flap-band .brand-tag{color:#fff;font-size:2.6px}
</style>
</head>
<body>

  <section class="sheet letterhead">
    <div class="brand">
      <div class="brand-row"><span class="brand-square"></span><span class="brand-name">VALE 8</span></div>
      <div class="brand-tag">CPAs and Tax Advisors</div>
    </div>
    <div class="letter-body">
      <p class="salute">Dear customer,</p>
      <p>Lorem ipsum dolor sit amet, consectetur adipisicing elit, sed do eiusmod tempor incididunt ut labore et dolore magna aliqua. Ut enim ad minim veniam, quis nostrud exercitation ullamco laboris nisi ut aliquip ex ea commodo consequat. Duis aute irure dolor in reprehenderit in voluptate velit esse cillum dolore eu fugiat nulla pariatur. Excepteur sint occaecat cupidatat non proident, sunt in culpa qui officia deserunt mollit anim id est laborum.</p>
      <p>Lorem ipsum dolor sit amet, consectetur adipisicing elit, sed do eiusmod tempor incididunt ut labore et dolore magna aliqua. Ut enim ad minim veniam, quis nostrud exercitation ullamco laboris nisi ut aliquip ex ea commodo consequat. Duis aute irure dolor in reprehenderit in voluptate velit esse cillum dolore eu fugiat nulla pariatur. Excepteur sint occaecat cupidatat non proident, sunt in culpa qui officia deserunt mollit anim id est laborum.</p>
      <p>Lorem ipsum dolor sit amet, consectetur adipisicing elit, sed do eiusmod tempor incididunt ut labore et dolore magna aliqua. Ut enim ad minim veniam, quis nostrud exercitation ullamco laboris nisi ut aliquip ex ea commodo consequat. Duis aute irure dolor in reprehenderit in voluptate velit esse cillum dolore eu fugiat nulla pariatur. Excepteur sint occaecat cupidatat non proident, sunt in culpa qui officia deserunt mollit anim id est laborum.</p>
      <p>Lorem ipsum dolor sit amet, consectetur adipisicing elit, sed do eiusmod tempor incididunt ut labore et dolore magna aliqua. Ut enim ad minim veniam, quis nostrud exercitation ullamco laboris nisi ut aliquip ex ea commodo consequat. Duis aute irure dolor in reprehenderit.</p>
      <p>Yours Sincerely,</p>
    </div>
    <footer class="letter-credentials">
      <div>48 Orchard Bend Road, Marlow Falls, GA 30412</div>
      <div class="contact-line">
        <span><svg class="icon" viewBox="0 0 10 10"><path d="M2 0.5l2 2-1 1.2c.6 1.3 1.6 2.3 2.9 2.9l1.2-1 2 2L8 9.5C4 9.5.5 6 .5 2z"/></svg>+14045550182</span>
        <span><svg class="icon" viewBox="0 0 10 10"><path d="M0 2h10v6H0z M0 2l5 3.5L10 2" fill="none" stroke="#1b1c1f" stroke-width="1.2"/></svg>info@valeeight.com</span>
        <span><svg class="icon" viewBox="0 0 10 10"><circle cx="5" cy="5" r="4.2" fill="none" stroke="#1b1c1f" stroke-width="1"/><path d="M.8 5h8.4M5 .8v8.4" stroke="#1b1c1f" stroke-width=".8"/></svg>www.valeeight.com</span>
      </div>
    </footer>
  </section>

  <section class="sheet folder">
    <div class="folder-spine"></div>
    <div class="brand">
      <div class="brand-row"><span class="brand-square"></span><span class="brand-name">VALE 8</span></div>
      <div class="brand-tag">CPAs and Tax Advisors</div>
    </div>
    <div class="folder-photo" role="img" aria-label="Photo of two advisors reviewing figures on a laptop in a bright office, framed by dark and blue angled panels"></div>
    <div class="folder-url">www.<b>valeeight</b>.com</div>
  </section>

  <section class="sheet card-front">
    <div class="brand">
      <div class="brand-row"><span class="brand-square"></span><span class="brand-name">VALE 8</span></div>
      <div class="brand-tag">CPAs and Tax Advisors</div>
    </div>
    <span class="card-divider"></span>
    <div class="card-details">
      <div class="card-name">MARTIN ELLERY</div>
      <div class="card-role">Managing Director</div>
      <div>48 Orchard Bend Road,</div>
      <div>Marlow Falls, GA 30412</div>
      <div>+14045550182</div>
      <div>info@valeeight.com</div>
      <div>www.valeeight.com</div>
    </div>
  </section>

  <section class="sheet card-back" role="img" aria-label="Card reverse with a dark repeating pattern and one blue accent"></section>

  <section class="sheet envelope-plain">
    <div class="brand">
      <div class="brand-row"><span class="brand-square"></span><span class="brand-name">VALE 8</span></div>
      <div class="brand-tag">CPAs and Tax Advisors</div>
    </div>
    <div class="envelope-address">48 Orchard Bend Road,<br>Marlow Falls, GA 30412</div>
  </section>

  <section class="sheet envelope-flap">
    <div class="flap-band">
      <div class="brand">
        <div class="brand-row"><span class="brand-square"></span><span class="brand-name">VALE 8</span></div>
        <div class="brand-tag">CPAs and Tax Advisors</div>
      </div>
    </div>
  </section>

</body>
</html>
```